creation of a business card design for a company specializing in the creation...

I would like to create a design for a professional business card on a black background and with the company's colors (I am attaching some files: including the logo in horizontal and centered format, I am also attaching a recent project design a T-shirt, this is the one I chose to give you an idea of my preferences.

we are in the process of developing a new website design, it is still in the development phase but it can be viewed at the following address: www.vantrelmo.be to give you other ideas about the company
you will see for yourself the subject of my main activity: company specializing in the construction of stairs

I would like a business card that stands out from the rest with a unique design

here is the informations
Name: Lucien Barthel
Function: Manager
Address: Rue Moulinet du Parc 42
7180 La Louvière
telephone: +32 468 219 804
email: info@rx7p.be
website: rx7p. be
social networks: Facebook, YouTube, TikTok, Instagram

Target Market(s)

customer who wants to have a beautiful staircase built

Industry/Entity Type

contruction d'escalier

Contact Information for Business Card

Adresse. Numero de telephone, site web, le texte : "Createur d'escalier", logo recto-verso, icone des reseaux sociaux

Requirements
Must have
• the mention: Stair creator
Nice to have
• an illustration of a designer staircase
Should not have
• do not distort the logo

```html
<!DOCTYPE html>
<html lang="fr">
<head>
<meta charset="utf-8">
<title>RX7P – Business card</title>
<link href="https://fonts.googleapis.com/css2?family=Montserrat:wght@400;500;700&display=swap" rel="stylesheet">
<style>
  :root {
    --stage: #151515;
    --card: #2a2a2c;
    --accent: #6b9bbb;
    --accent-light: #9dbfd4;
    --text: #f2f2f2;
    --watermark: rgba(62, 70, 74, 0.55);
  }
  * { margin: 0; padding: 0; box-sizing: border-box; }
  html, body {
    width: 1200px; height: 1059px; overflow: hidden;
    background: var(--stage);
    font-family: "Montserrat", sans-serif;
  }
  .card {
    position: absolute;
    background: var(--card);
    border-radius: 18px;
    overflow: hidden;
  }
  .card--front { left: 257px; top: 89px; width: 687px; height: 390px; }
  .card--back  { left: 254px; top: 547px; width: 693px; height: 393px; }

  .stair-decor {
    position: absolute; left: 307px; top: 193px; right: 0; bottom: 0;
    background: radial-gradient(ellipse at 62% 55%, var(--watermark) 0%, rgba(62,70,74,0.25) 45%, rgba(62,70,74,0) 72%);
  }

  .name-bar {
    position: absolute; left: 0; top: 68px;
    width: 18px; height: 42px; background: var(--accent);
  }
  .holder { position: absolute; left: 44px; top: 62px; }
  .holder__name {
    font-weight: 700; font-size: 26px; color: var(--accent);
    letter-spacing: 0.3px; line-height: 1.1;
  }
  .holder__role { font-size: 17px; color: var(--text); line-height: 1.2; }

  .address {
    position: absolute; left: 44px; top: 203px;
    font-size: 17px; line-height: 22px; color: var(--text);
    letter-spacing: 0.3px;
  }
  .contacts {
    position: absolute; left: 44px; top: 268px;
    list-style: none; color: var(--text); font-size: 18px;
    letter-spacing: 0.3px;
  }
  .contacts li { display: flex; align-items: center; height: 26.5px; }
  .contacts svg { width: 13px; height: 13px; margin-right: 8px; fill: var(--accent-light); }

  .brand { position: absolute; display: flex; align-items: center; }
  .brand__mark { background: var(--accent); }
  .brand__name { color: var(--text); font-weight: 400; letter-spacing: 6px; line-height: 1; }

  .card--front .brand { right: 38px; top: 60px; gap: 14px; }
  .card--front .brand__mark { width: 28px; height: 28px; }
  .card--front .brand__name { font-size: 34px; }

  .tagline {
    position: absolute; color: var(--accent-light);
    font-weight: 500; text-transform: uppercase; white-space: nowrap; line-height: 1;
  }
  .card--front .tagline { right: 38px; top: 100px; font-size: 9px; letter-spacing: 3.5px; }

  .card--back .brand { left: 50%; top: 153px; transform: translateX(-50%); gap: 26px; }
  .card--back .brand__mark { width: 56px; height: 56px; }
  .card--back .brand__name { font-size: 64px; letter-spacing: 12px; }
  .card--back .tagline { left: 437px; top: 220px; transform: translateX(-50%); font-size: 14px; letter-spacing: 7px; }

  .socials {
    position: absolute; left: 50%; top: 321px; transform: translateX(-50%);
    display: flex; gap: 7px; list-style: none;
  }
  .socials li {
    width: 28px; height: 28px; border-radius: 50%; background: var(--accent);
  }
</style>
</head>
<body>
  <section class="card card--front">
    <div class="stair-decor" role="img" aria-label="Illustration d'escalier en filigrane"></div>

    <div class="name-bar"></div>
    <div class="holder">
      <p class="holder__name">Lucien Barthel</p>
      <p class="holder__role">Manager</p>
    </div>

    <div class="brand">
      <span class="brand__mark"></span>
      <span class="brand__name">RX7P</span>
    </div>
    <p class="tagline">Stair creator</p>

    <p class="address">Rue Moulinet du Parc 42<br>7180 La Louvière</p>

    <ul class="contacts">
      <li>
        <svg viewBox="0 0 16 16" aria-hidden="true"><path d="M1 6c0-2 3-3.5 7-3.5S15 4 15 6l-3 1-.6-2H4.6L4 7zM4 8h8l2 6H2z"/></svg>
        +32 468 219 804
      </li>
      <li>
        <svg viewBox="0 0 16 16" aria-hidden="true"><path d="M1 6l7-5 7 5v9H1zM2.5 7v6.5h11V7L8 11z"/></svg>
        info@rx7p.be
      </li>
      <li>
        <svg viewBox="0 0 16 16" aria-hidden="true"><circle cx="8" cy="8" r="7"/></svg>
        www.rx7p.be
      </li>
    </ul>
  </section>

  <section class="card card--back">
    <div class="brand">
      <span class="brand__mark"></span>
      <span class="brand__name">RX7P</span>
    </div>
    <p class="tagline">Stair creator</p>
    <ul class="socials" aria-label="Réseaux sociaux">
      <li></li><li></li><li></li><li></li>
    </ul>
  </section>
</body>
</html>
```